Business card design for a dynamic IT consulting company

We need a business card design for a young firm, specialized in the Telecommunications/Consulting industry. The name of the company is Quindor and Partners Business Consulting Ltd. (Short name: Quindor and Partnes)
Quindor = solve read reverse, so we aim to be uncomplicated and solution-oriented. The small pipe in our logo is also related to the word solve. So we need a new business card design, which is simple, eye catching and something non traditional (I would probably prefer a square shaped design rather than a rectangle, but open for suggestions). Attached our logo.

Target Market(s)

Usually our customers are Tier1 Telecoms providers (Q-Netra, Palorix, etc) and their executives.

Industry/Entity Type

Business

Contact Information for Business Card

Name: Bence Tolnavari
Email: b.tolnavari@quindor.hu
Web: www.quindor.hu
Mobile: +36 30 518 2769
Title: Managing Director

Optional:
Company name: Quindor and Partners Ltd.
Address: 1087 Budapest, Tolvenka str. 28/C, Hungary

Font styles to use
Other font styles liked:
• helveticaneue_medium, Prime Regular are used now.

Colors

Designer to choose colors to be used in the design.

Requirements
Must have
• I would like to have a 2 sided design.
Nice to have
• I thought if we make the logo a bit bigger (without the company name), that could go to the back with the company name below. I though, if the pipe in the logo is somehow touchable on the business card, would be nice and unique.

```html
<!DOCTYPE html>
<html lang="en">
<head>
<meta charset="utf-8">
<title>Quindor &amp; Partners – Business Card</title>
<link href="https://fonts.googleapis.com/css2?family=Work+Sans:wght@400;500&family=Exo+2:wght@600&display=swap" rel="stylesheet">
<style>
  :root {
    --bg: #d9d9d9;
    --card: #262626;
    --card-back: #232323;
    --ink: #f2f2f2;
    --muted: #d4d4d4;
    --blue: #1c9ad6;
    --emboss: #3b3b3b;
  }
  * { margin: 0; padding: 0; box-sizing: border-box; }
  html, body { width: 1200px; height: 900px; overflow: hidden; background: var(--bg); }
  .canvas { position: relative; width: 1200px; height: 900px; }
  .card {
    position: absolute; left: 240px; width: 720px; height: 410px;
    border-radius: 3px; overflow: hidden;
    box-shadow: 0 6px 18px rgba(0,0,0,.25);
    font-family: "Work Sans", Arial, sans-serif;
  }
  .card--back { top: 30px; background: var(--card-back); }
  .card--front { top: 460px; background: var(--card); color: var(--ink); }

  .brand { display: flex; align-items: center; gap: 12px; font-weight: 500; }
  .brand__square { width: 14px; height: 14px; }
  .card--back .brand {
    position: absolute; left: 0; right: 0; top: 0; bottom: 0;
    justify-content: center; font-size: 46px; color: var(--emboss);
  }
  .card--back .brand__square { width: 26px; height: 26px; background: var(--emboss); }
  .card--front .brand { position: absolute; left: 38px; top: 36px; font-size: 30px; color: var(--ink); }
  .card--front .brand__square { background: var(--blue); }

  .rule { position: absolute; left: 70px; top: 196px; width: 450px; height: 1px; background: var(--blue); }
  .footer-band { position: absolute; left: 0; right: 0; bottom: 0; height: 22px; background: var(--blue); }

  .person { position: absolute; right: 40px; top: 198px; text-align: right; }
  .person__name { font-family: "Exo 2", Arial, sans-serif; font-weight: 600; font-size: 27px; line-height: 1.15; color: var(--blue); letter-spacing: .5px; }
  .person__title { font-size: 19px; color: var(--muted); margin-top: 2px; letter-spacing: .3px; }

  .contacts { position: absolute; left: 48px; top: 236px; list-style: none; font-size: 18px; color: var(--ink); }
  .contacts li { display: flex; align-items: center; gap: 14px; height: 26px; }
  .contacts svg { width: 14px; height: 14px; flex: none; }

  .address { position: absolute; right: 70px; top: 296px; text-align: right; font-size: 19px; line-height: 1.35; color: var(--ink); font-style: normal; }
</style>
</head>
<body>
<main class="canvas">
  <section class="card card--back" aria-label="Card back">
    <div class="brand"><span class="brand__square"></span><span>Quindor &amp; Partners</span></div>
  </section>

  <section class="card card--front" aria-label="Card front">
    <div class="rule"></div>
    <div class="footer-band"></div>

    <div class="brand"><span class="brand__square"></span><span>Quindor &amp; Partners</span></div>

    <div class="person">
      <div class="person__name">Bence Tolnavari</div>
      <div class="person__title">Managing Director</div>
    </div>

    <ul class="contacts">
      <li>
        <svg viewBox="0 0 16 16"><path d="M4 1 L6.5 4.5 L5 6 C6 8.5 7.5 10 10 11 L11.5 9.5 L15 12 L13 15 C6.5 14.5 1.5 9.5 1 3 Z" fill="var(--blue)"/></svg>
        <span>+36 30 518 2769</span>
      </li>
      <li>
        <svg viewBox="0 0 16 16"><rect x="1" y="3" width="14" height="10" fill="none" stroke="var(--blue)" stroke-width="1.5"/><path d="M1 3 L8 9 L15 3" fill="none" stroke="var(--blue)" stroke-width="1.5"/></svg>
        <span>b.tolnavari@quindor.hu</span>
      </li>
      <li>
        <svg viewBox="0 0 16 16"><circle cx="8" cy="8" r="6.5" fill="none" stroke="var(--blue)" stroke-width="1.4"/><ellipse cx="8" cy="8" rx="2.8" ry="6.5" fill="none" stroke="var(--blue)" stroke-width="1.2"/><line x1="1.5" y1="8" x2="14.5" y2="8" stroke="var(--blue)" stroke-width="1.2"/></svg>
        <span>www.quindor.hu</span>
      </li>
    </ul>

    <address class="address">1087 Budapest,<br>Tolvenka str. 28/C, Hungary</address>
  </section>
</main>
</body>
</html>
```